Brisk Haven - Business Card

Modern Business Card : I like a simple, clean designs. Think Pear!

Information to Include
Brisk Haven Inc. (Logo)
Name: Ned Farrow
Position: President
Office: 555-318-2046
Fax: 555-318-2046
Cell: 555-318-2046
E-Mail: nfarrow@thebriskhaven.example
Website: www.thebriskhaven.example

I attached the "guardnet.example" dealer logo. This logo is not a requirement, but a plus if it looks good with the design.

I also have access to more pictures and logos, if you see something on guardnet.example
or vexlo.example, I can probably get the file. Again, this is not mandatory.

```html
<!DOCTYPE html>
<html lang="en">
<head>
<meta charset="utf-8">
<title>Brisk Haven – Business Card</title>
<link rel="stylesheet" href="https://fonts.googleapis.com/css2?family=Open+Sans:wght@300;400;600;700&display=swap">
<style>
  :root {
    --orange: #d35f2a;
    --black: #0b0b0b;
    --ink: #222222;
    --paper: #ffffff;
    --paper-shade: #ececec;
    --backdrop: #e4e4e4;
  }
  * { box-sizing: border-box; margin: 0; padding: 0; }
  html, body {
    width: 1200px; height: 940px; overflow: hidden;
    background: var(--backdrop);
    font-family: "Open Sans", Arial, sans-serif;
  }
  .canvas {
    width: 1200px; height: 940px;
    display: flex; align-items: center; justify-content: center;
  }
  .card {
    position: relative;
    width: 1000px; height: 572px;
    background: radial-gradient(ellipse at 62% 40%, var(--paper) 0%, #f7f7f7 50%, var(--paper-shade) 100%);
    overflow: hidden;
    box-shadow: 0 10px 30px rgba(0,0,0,.18);
  }
  /* top edge bands */
  .band { position: absolute; background: var(--black); }
  .band--top-left { left: 0; top: 0; width: 62px; height: 30px; }
  .band--top-right { left: 372px; top: 0; right: 0; height: 32px; }
  .band--bottom-left { left: 0; bottom: 0; width: 72px; height: 40px; }
  .band--bottom-right { left: 420px; bottom: 0; right: 0; height: 42px; }
  .tab { position: absolute; background: var(--orange); }
  .tab--top { left: 70px; top: 0; width: 296px; height: 46px; border-radius: 0 0 10px 10px; }
  .tab--bottom { left: 80px; bottom: 0; width: 334px; height: 58px; border-radius: 10px 10px 0 0; }
  .pointer { position: absolute; left: 0; top: 118px; width: 70px; height: 46px; }

  .identity { position: absolute; left: 92px; top: 84px; color: var(--orange); }
  .identity__name { font-weight: 300; font-size: 54px; letter-spacing: 1px; line-height: 1.1; text-transform: uppercase; }
  .identity__role { font-weight: 400; font-size: 20px; margin-top: 6px; }

  .contacts { position: absolute; left: 100px; top: 238px; list-style: none; }
  .contact { display: flex; align-items: center; gap: 22px; height: 80px; }
  .contact__icon { width: 34px; height: 34px; flex: none; }
  .contact__text { font-size: 22px; line-height: 1.3; color: var(--ink); }

  .brand { position: absolute; left: 560px; top: 178px; display: flex; align-items: center; gap: 20px; }
  .brand__mark { width: 44px; height: 44px; background: var(--orange); }
  .brand__name { font-weight: 700; font-size: 48px; color: var(--ink); letter-spacing: -0.5px; }
</style>
</head>
<body>
<div class="canvas">
  <article class="card">
    <div class="band band--top-left"></div>
    <div class="tab tab--top"></div>
    <div class="band band--top-right"></div>
    <div class="band band--bottom-left"></div>
    <div class="tab tab--bottom"></div>
    <div class="band band--bottom-right"></div>

    <svg class="pointer" viewBox="0 0 70 46" aria-hidden="true">
      <polygon points="0,0 50,0 70,23 50,46 0,46" fill="var(--orange)"/>
    </svg>

    <header class="identity">
      <h1 class="identity__name">Ned Farrow</h1>
      <p class="identity__role">President</p>
    </header>

    <ul class="contacts">
      <li class="contact">
        <svg class="contact__icon" viewBox="0 0 34 34" aria-hidden="true">
          <path d="M17 4 L2 17 H6 V30 H14 V21 H20 V30 H28 V17 H32 Z" fill="var(--orange)"/>
        </svg>
        <p class="contact__text">48 Larkfield Road,<br>Northvale 2210</p>
      </li>
      <li class="contact">
        <svg class="contact__icon" viewBox="0 0 34 34" aria-hidden="true">
          <g fill="none" stroke="var(--orange)" stroke-width="2.4">
            <circle cx="17" cy="17" r="14"/>
            <ellipse cx="17" cy="17" rx="6" ry="14"/>
            <line x1="3" y1="17" x2="31" y2="17"/>
            <line x1="5" y1="10" x2="29" y2="10"/>
            <line x1="5" y1="24" x2="29" y2="24"/>
          </g>
        </svg>
        <p class="contact__text">nfarrow@thebriskhaven.example<br>www.thebriskhaven.example</p>
      </li>
      <li class="contact">
        <svg class="contact__icon" viewBox="0 0 34 34" aria-hidden="true">
          <path d="M9 4 L14 4 L16 11 L12 14 C14 19 16 22 21 24 L24 20 L31 22 L31 27 C31 29 29 31 27 31 C15 30 4 19 3 7 C3 5 5 4 9 4 Z" fill="var(--orange)"/>
        </svg>
        <p class="contact__text">555-318-2046<br>555-318-2046</p>
      </li>
    </ul>

    <div class="brand">
      <span class="brand__mark" aria-hidden="true"></span>
      <span class="brand__name">Brisk Haven</span>
    </div>
  </article>
</div>
</body>
</html>
```